Tolbek cards

I want a simple business card that pops.
Logo on one side.
On side two i want.
"Are you thinking about a new building on your property, or renovating an existing structure? Contact".....
Owners Name: Dale Whitacre
Owners Phone number: 610-555-0187
Address:4076 Copper Ridge RD, Ashgrove, PA 17384
Committed to Quality, Service, and Integrity

```html
<!DOCTYPE html>
<html lang="en">
<head>
<meta charset="utf-8">
<title>Tolbek Builders LLC – Business Cards</title>
<link href="https://fonts.googleapis.com/css2?family=Poppins:wght@400;600;700&display=swap" rel="stylesheet">
<style>
  :root{
    --brown:#422e1d;
    --ink:#1c1410;
    --paper:#ffffff;
    --stage:#f0f0f0;
    --swoosh-edge:#b89878;
    --swoosh-mid:#5a3a20;
  }
  *{margin:0;padding:0;box-sizing:border-box}
  html,body{width:1200px;height:990px;overflow:hidden;background:var(--stage);font-family:"Poppins",sans-serif}
  .card{position:absolute;left:244px;width:712px;height:407px;overflow:hidden}
  .card--front{top:68px;background:var(--brown)}
  .card--back{top:515px;background:var(--paper)}

  .brand{position:absolute;left:0;width:100%;display:flex;flex-direction:column;align-items:center}
  .brand-mark{background:var(--paper)}
  .brand-name{font-weight:700;line-height:1;text-align:center;white-space:nowrap}
  .brand-sub{font-weight:600;line-height:1;text-align:center;white-space:nowrap}

  .card--front .brand{top:80px}
  .card--front .brand-mark{width:134px;height:134px}
  .card--front .brand-name{font-size:82px;color:var(--paper);margin-top:16px;letter-spacing:1px}
  .card--front .brand-sub{font-size:29px;color:var(--paper);letter-spacing:2px;margin-top:4px}

  .card--back .brand{top:78px}
  .card--back .brand-mark{width:68px;height:68px;background:var(--brown)}
  .card--back .brand-name{font-size:39px;color:var(--brown);margin-top:3px}
  .card--back .brand-sub{font-size:12px;color:var(--brown);letter-spacing:1px;margin-top:1px}

  .pitch{position:absolute;top:19px;left:0;width:100%;text-align:center;font-size:19.2px;line-height:25px;color:var(--ink)}
  .owner{position:absolute;top:220px;left:20px;width:300px;text-align:right}
  .owner-name{font-size:38px;font-weight:600;line-height:44px;color:var(--brown);white-space:nowrap}
  .owner-role{font-size:18px;line-height:22px;color:var(--ink)}
  .divider{position:absolute;left:355px;top:212px;width:1.5px;height:85px;background:var(--brown)}
  .contact{position:absolute;left:388px;top:224px;font-size:18px;line-height:24.5px;color:var(--ink);list-style:none}
  .contact li{display:flex;gap:10px;align-items:flex-start}
  .contact svg{flex:none;width:16px;height:18px;margin-top:3px;fill:var(--brown)}
  .band{position:absolute;left:0;top:0;width:712px;height:407px}
  .tagline{position:absolute;top:349px;left:0;width:100%;text-align:center;font-size:19.2px;line-height:26px;color:var(--paper)}
</style>
</head>
<body>
  <section class="card card--front">
    <div class="brand">
      <div class="brand-mark"></div>
      <div class="brand-name">TOLBEK</div>
      <div class="brand-sub">BUILDERS LLC</div>
    </div>
  </section>

  <section class="card card--back">
    <svg class="band" viewBox="0 0 712 407" aria-hidden="true">
      <defs>
        <linearGradient id="swoosh" x1="0" x2="1">
          <stop offset="0" stop-color="var(--swoosh-edge)"/>
          <stop offset=".5" stop-color="var(--swoosh-mid)"/>
          <stop offset="1" stop-color="var(--swoosh-edge)"/>
        </linearGradient>
      </defs>
      <path d="M0 281 Q356 409 712 281 L712 407 L0 407 Z" fill="var(--brown)"/>
      <path d="M25 281 Q356 399 687 281" fill="none" stroke="url(#swoosh)" stroke-width="3.5"/>
    </svg>

    <p class="pitch">"Are you thinking about a new building on your property,<br>or renovating an existing structure? Contact"…..</p>

    <div class="brand">
      <div class="brand-mark"></div>
      <div class="brand-name">TOLBEK</div>
      <div class="brand-sub">BUILDERS LLC</div>
    </div>

    <div class="owner">
      <div class="owner-name">Dale Whitacre</div>
      <div class="owner-role">Owners</div>
    </div>
    <div class="divider"></div>
    <ul class="contact">
      <li>
        <svg viewBox="0 0 24 24"><path d="M6.6 10.8a15.2 15.2 0 0 0 6.6 6.6l2.2-2.2c.3-.3.7-.4 1-.2 1.1.4 2.3.6 3.6.6.6 0 1 .4 1 1V20c0 .6-.4 1-1 1A17 17 0 0 1 3 4c0-.6.4-1 1-1h3.5c.6 0 1 .4 1 1 0 1.3.2 2.5.6 3.6.1.3 0 .7-.2 1z"/></svg>
        <span>610-555-0187</span>
      </li>
      <li>
        <svg viewBox="0 0 24 24"><path d="M12 2a7 7 0 0 0-7 7c0 5 7 13 7 13s7-8 7-13a7 7 0 0 0-7-7zm0 9.5a2.5 2.5 0 1 1 0-5 2.5 2.5 0 0 1 0 5z"/></svg>
        <span>4076 Copper Ridge RD, Ashgrove,<br>PA 17384</span>
      </li>
    </ul>

    <p class="tagline">Committed to Quality, Service, and Integrity</p>
  </section>
</body>
</html>
```